New Webpage for High Class Expert Witness Services Company

We are looking for a minimalist design for a webpage that just has our logo and an entry form offer to connect with one of our Liaisons.
The entry form should just ask for Name, Email, Contact Info and Description of Project.

Company Name is: The Marlowe Crest Advisory Services

Number of Pages Required

1 page

```html
<!DOCTYPE html>
<html lang="en">
<head>
<meta charset="utf-8">
<title>Marlowe Crest Advisory Services — Connect with a Liaison</title>
<link href="https://fonts.googleapis.com/css2?family=Cinzel:wght@400;600&family=Roboto:wght@400&display=swap" rel="stylesheet">
<style>
  :root {
    --bg-deep: #0b0b0c;
    --bg-lift: #1c1c1e;
    --text-bright: #f4f4f4;
    --text-muted: #a3a3a3;
    --text-footer: #b5b5b5;
    --rule: #4a4a4a;
    --field-border: #cfcfcf;
    --panel-border: #5a5a5a;
    --button-light: #e2e2e4;
    --button-shade: #9c9ca0;
    --button-text: #111111;
  }
  * { box-sizing: border-box; margin: 0; padding: 0; }
  html, body { width: 1200px; height: 742px; overflow: hidden; }
  body {
    position: relative;
    background:
      radial-gradient(ellipse 520px 420px at 960px 330px, rgba(60,60,62,0.45), transparent 70%),
      radial-gradient(ellipse 700px 500px at 80px 40px, rgba(45,45,47,0.35), transparent 70%),
      linear-gradient(135deg, var(--bg-lift) 0%, var(--bg-deep) 45%, var(--bg-deep) 70%, #161617 100%);
    color: var(--text-bright);
    font-family: "Roboto", Arial, sans-serif;
  }
  .brand {
    position: absolute; left: 114px; top: 50px;
    display: flex; align-items: center; gap: 14px;
    font-family: "Cinzel", Georgia, serif; font-weight: 400;
    font-size: 26px; letter-spacing: 1.5px; color: var(--text-bright);
  }
  .brand-mark { width: 26px; height: 26px; background: var(--text-bright); }
  .eyebrow {
    position: absolute; left: 111px; top: 219px;
    font-family: "Cinzel", Georgia, serif; font-size: 15.5px;
    letter-spacing: 2px; color: var(--text-muted);
  }
  .headline {
    position: absolute; left: 114px; top: 260px;
    border-left: 1px solid var(--rule); padding-left: 22px;
    font-family: "Cinzel", Georgia, serif; font-weight: 400;
    font-size: 50px; line-height: 50px; letter-spacing: 1px;
    color: var(--text-bright); height: 147px;
  }
  .liaison-panel {
    position: absolute; left: 715px; top: 124px; width: 378px; height: 437px;
    border: 1px solid var(--panel-border);
    background: rgba(10,10,10,0.35);
    padding: 33px 0 0 46px;
  }
  .liaison-title {
    font-family: "Cinzel", Georgia, serif; font-weight: 400;
    font-size: 22px; letter-spacing: 0.5px; color: var(--text-bright);
    margin-bottom: 27px; text-align: center; width: 298px;
  }
  .liaison-form { display: flex; flex-direction: column; gap: 0; }
  .field {
    width: 294px; height: 42px; margin-bottom: 15px;
    background: transparent; border: 1px solid var(--field-border); border-radius: 1px;
    padding: 0 18px; color: var(--text-bright);
    font-family: "Roboto", Arial, sans-serif; font-size: 13px;
  }
  .field::placeholder { color: var(--text-bright); opacity: 1; }
  .field-area { height: 88px; padding-top: 12px; resize: none; margin-bottom: 13px; }
  .submit {
    width: 298px; height: 44px; border: none; border-radius: 2px; cursor: pointer;
    background: linear-gradient(110deg, var(--button-light) 0%, var(--button-light) 30%, #f3f3f4 45%, var(--button-shade) 65%, var(--button-shade) 100%);
    font-family: "Cinzel", Georgia, serif; font-weight: 600; font-size: 15px;
    letter-spacing: 0.5px; color: var(--button-text);
  }
  .site-footer {
    position: absolute; left: 0; top: 680px; width: 1200px; height: 62px;
    border-top: 1px solid #2e2e2e;
    display: flex; align-items: center; justify-content: center;
    font-size: 12.5px; color: var(--text-footer);
  }
</style>
</head>
<body>
  <header class="brand">
    <span class="brand-mark"></span>
    <span class="brand-name">Marlowe Crest</span>
  </header>

  <p class="eyebrow">MARLOWE CREST ADVISORY SERVICES</p>
  <h1 class="headline">SEAMLESS<br>MEDICAL EXPERT<br>INTEGRATION</h1>

  <section class="liaison-panel">
    <h2 class="liaison-title">Connect with a Liaison</h2>
    <form class="liaison-form">
      <input class="field" type="text" placeholder="Name*">
      <input class="field" type="email" placeholder="Email*">
      <input class="field" type="tel" placeholder="Phone number*">
      <textarea class="field field-area" placeholder="Description of Project"></textarea>
      <button class="submit" type="submit">SUBMIT</button>
    </form>
  </section>

  <footer class="site-footer">© 2026 Marlowe Crest Advisory Services. All Rights Reserved</footer>
</body>
</html>
```